Need CATCHY/VIVID Banner design for my new UTV/ATV/Off Road Vehicle turn signal/lighting company

I need a banner ad designed so I can advertise on several different ATV (all terrain vehicle), UTV (Utility Vehicles), Golf Cart and Off-Road Vehicle forums. Ads need to be very catchy and produce a call to action. Action is getting hits to my website. Our main business is selling turn signal kits to make your side by side or your ATV/UTV street legal, as some states now allow you to drive these on public roads if you have the following items: Turn Signals, Horn, Lighted license plate bracket, headlights and brake lights. We sell all of these items for just about any model vehicle out there. Our call to action for this banner would be to get more website visits.

Target Market(s)

Off-road/outdoor enthusiasts,

Industry/Entity Type

Car Accessorie

Font styles to use
Sans Serif

Requirements
Must have
• Ad size need to be either 728x90 or 300x250. Colorful ad with an off-road vehicle integrated to the design (think UTV, side-by-side, etc.
Nice to have
• Nice to haves would be anything that makes this banner ad stand out on very boring web pages.
Should not have
• anything dull

```html
<!DOCTYPE html>
<html lang="en">
<head>
<meta charset="utf-8">
<title>TrailFlash – ATV &amp; UTV Signal Kits Banner</title>
<link rel="stylesheet" href="https://fonts.googleapis.com/css2?family=Archivo:wght@800;900&family=Montserrat:wght@700;800&display=swap">
<style>
  :root{
    --ink:#0b0b0c;
    --white:#ffffff;
    --yellow:#f5c400;
    --red:#d0121b;
    --red-deep:#7a0a0e;
    --sky:#9cb9cf;
    --sand:#c89a62;
    --rock:#6e5440;
  }
  *{margin:0;padding:0;box-sizing:border-box}
  html,body{width:1200px;height:1000px;overflow:hidden;background:var(--ink)}
  .banner{position:relative;width:1200px;height:1000px;overflow:hidden}
  .scene{position:absolute;inset:0;
    background:
      radial-gradient(ellipse 420px 380px at 900px 560px, rgba(20,16,16,.95), rgba(20,16,16,0) 75%),
      linear-gradient(180deg, var(--sky) 0%, #d6c3a4 28%, var(--sand) 45%, var(--rock) 78%, #3e2e24 100%);}
  .overlay{position:absolute;inset:0}
  .brand{position:absolute;left:46px;top:40px;display:flex;align-items:center;gap:18px}
  .brand-dot{width:46px;height:46px;border-radius:50%;background:var(--yellow)}
  .brand-name{font-family:"Montserrat",sans-serif;font-weight:800;font-size:64px;color:var(--yellow);letter-spacing:1px}
  .brand-tag{position:absolute;left:42px;top:150px;font-family:"Archivo",sans-serif;font-weight:800;color:var(--white);line-height:1.02}
  .brand-tag .l1{font-size:44px;letter-spacing:.5px}
  .brand-tag .l2{font-size:31px;letter-spacing:.4px}
  .headline{position:absolute;left:42px;top:456px;font-family:"Archivo",sans-serif;font-weight:900;color:var(--white);font-size:114px;line-height:1;letter-spacing:1px}
  .subline{position:absolute;left:46px;top:700px;font-family:"Montserrat",sans-serif;font-weight:800;color:var(--yellow);font-size:44px;line-height:1.32;letter-spacing:1px}
  .features{position:absolute;left:62px;top:856px;display:flex;gap:42px}
  .feature{width:126px;height:126px;border-radius:50%;background:var(--yellow);display:flex;align-items:center;justify-content:center}
  .feature svg{width:80px;height:80px}
</style>
</head>
<body>
<div class="banner">
  <div class="scene" role="img" aria-label="Photo of a red and black sport side-by-side UTV on desert rocks with mountains and blue sky behind"></div>

  <svg class="overlay" viewBox="0 0 1200 1000" aria-hidden="true">
    <defs>
      <linearGradient id="shade" x1="0" x2="1" y1="0" y2="0">
        <stop offset="0" stop-color="#0b0b0c" stop-opacity=".85"/>
        <stop offset=".55" stop-color="#0b0b0c" stop-opacity=".55"/>
        <stop offset=".8" stop-color="#0b0b0c" stop-opacity="0"/>
      </linearGradient>
    </defs>
    <rect width="1200" height="1000" fill="url(#shade)"/>
    <polygon points="0,0 660,0 560,140 0,420" fill="var(--red-deep)" opacity=".9"/>
    <polygon points="0,0 620,0 480,160 250,300 0,370" fill="var(--red)" opacity=".85"/>
    <polygon points="0,420 560,140 470,330 0,560" fill="var(--red)" opacity=".35"/>
  </svg>

  <div class="brand"><span class="brand-dot"></span><span class="brand-name">TRAILFLASH</span></div>
  <div class="brand-tag"><div class="l1">TURN SIGNAL KITS</div><div class="l2">&amp; LIGHTING ACCESSORIES</div></div>

  <h1 class="headline">ATV &amp; UTV<br>VECHICLE</h1>
  <p class="subline">SIGNAL KITS AND<br>LIGHTING ACCESSORIES</p>

  <div class="features">
    <div class="feature" aria-label="Brake lights">
      <svg viewBox="0 0 80 80" fill="none" stroke="#fff" stroke-width="6" stroke-linecap="round">
        <circle cx="40" cy="40" r="20"/><path d="M16 20a30 30 0 0 0 0 40M64 20a30 30 0 0 1 0 40"/><path d="M40 30v12"/><circle cx="40" cy="50" r="1.5" fill="#fff"/>
      </svg>
    </div>
    <div class="feature" aria-label="Headlights">
      <svg viewBox="0 0 80 80" fill="#fff" stroke="#fff" stroke-width="6" stroke-linecap="round">
        <path d="M46 18c14 0 20 10 20 22s-6 22-20 22z"/><path d="M34 24H12M34 36H12M34 48H12M34 60H12" fill="none"/>
      </svg>
    </div>
    <div class="feature" aria-label="Horn">
      <svg viewBox="0 0 80 80" fill="#fff">
        <path d="M8 34h12l44-18v48L20 46H8z"/><rect x="64" y="26" width="8" height="28" rx="2"/><rect x="22" y="46" width="10" height="18" rx="2"/>
      </svg>
    </div>
    <div class="feature" aria-label="Turn signals">
      <svg viewBox="0 0 80 80" fill="none" stroke="#fff" stroke-width="5" stroke-linejoin="round">
        <path d="M6 40l16-16v10h12v12H22v10z"/><path d="M74 40L58 24v10H46v12h12v10z"/>
      </svg>
    </div>
  </div>
</div>
</body>
</html>
```